Business card design needed

Family General Practitioner/ Family Physician.
Logo is the logo of the Noble Guild of Family Healers Oceania
http://kpltw.varendo.example/ImageShelf/marks/pages/NGFHO%20mark_jpg.htm
Updates

Project Deadline Extended
Reason: Just a bit more time to make changes and the weekend for me to look at things closely and to choose. Thanks, Orin

Thanks for all the submissions. So many of them are really works of art. Not one of them are not good. The ones that I am eliminating are the ones that I think are not suitable for me personally only, and because if I don't, it makes it very difficult to decide as many of you are also sending me slight variations of a card. I have just decided to choose a second place card too. Can't thank you all enough. Good luck, Orin. P.S - Working today till 10 pm as the card says :-), so probably won't be able to give a feedback till late Saturday night or Sunday morning here in Sydney, Australia. 

Project Deadline Extended
Reason: Just added a second place to the budget and realised that Australia is ahead of the rest of the world in the time zone (only :-) - don't want to offend anyone or start a debate!! ) , so Monday deadline will mean it will be a weekend for the rest of the world. Just wanted to give everyone more time to submit their best, especially since I will be picking a second card too. Can't thank everyone enough for the submissions. P.S - Not keen on photos on the card.

Industry/Entity Type

Business

Contact Information for Business Card

Dr. Orin Halvey M.B.B.S., F.N.G.F.H.O
Family General Practitioner
Address, timings, phone and fax number on the back.

Requirements
Must have
• Timings
Mon 7 am - 7 pm
Tues 7 am - 12 pm
Wed 7 am - 10 pm
Thurs 7 am - 12 pm
Fri 7 am - 8 pm
Sat 8 am - 10 pm
Sun - Off

```html
<!DOCTYPE html>
<html lang="en">
<head>
<meta charset="utf-8">
<title>Dr. Orin Halvey – Business Card Options</title>
<link rel="stylesheet" href="https://fonts.googleapis.com/css2?family=Cinzel:wght@400;500&family=Open+Sans:wght@400;700;800&family=Tinos:wght@400;700&display=swap">
<style>
  :root {
    --navy: #0b1540;
    --navy-deep: #070d2c;
    --glow: #2e63b8;
    --yellow: #ffe600;
    --orange: #e77a1b;
    --silver: #c9ccd4;
    --ink: #1a1208;
    --white: #ffffff;
    --page: #e9e4dc;
    --label: #3a2a1a;
    --mark: rgba(120, 150, 210, 0.16);
  }
  * { margin: 0; padding: 0; box-sizing: border-box; }
  html, body { width: 1200px; height: 739px; overflow: hidden; }
  body { position: relative; background: var(--page); }

  .card {
    position: absolute;
    width: 525px; height: 300px;
    overflow: hidden;
    background: radial-gradient(ellipse 260px 200px at 50% 45%, var(--glow) 0%, #16307a 35%, var(--navy) 70%, var(--navy-deep) 100%);
    box-shadow: 0 3px 8px rgba(0,0,0,0.25);
  }
  .card--front { left: 35px; top: 27px; }
  .card--opt1 { left: 615px; top: 27px; }
  .card--opt2 { left: 47px; top: 368px; }
  .card--opt3 { left: 612px; top: 375px; }

  /* Front */
  .front__swoosh { position: absolute; left: 0; top: 0; width: 525px; height: 300px; }
  .front__name {
    position: absolute; top: 48px; width: 100%; text-align: center;
    font-family: "Cinzel", serif; font-size: 40px; color: var(--white); letter-spacing: 1px;
  }
  .front__creds {
    position: absolute; top: 98px; width: 100%; text-align: center;
    font-family: "Tinos", serif; font-size: 11px; color: var(--white); letter-spacing: 1px;
  }
  .front__role {
    position: absolute; top: 143px; width: 100%; text-align: center;
    font-family: "Tinos", serif; font-size: 19px; color: var(--white); letter-spacing: 1.6px;
  }
  .front__tagline {
    position: absolute; left: 122px; top: 256px;
    font-family: "Tinos", serif; font-weight: 700; font-size: 22px; color: var(--ink);
  }
  .guild-mark {
    position: absolute; left: 420px; top: 212px; width: 100px;
    display: flex; flex-direction: column; align-items: center; gap: 4px;
    font-family: "Tinos", serif; font-size: 9px; line-height: 1.15; color: var(--navy); text-align: center;
  }
  .guild-mark__dot { width: 22px; height: 22px; border-radius: 50%; background: var(--navy); }

  /* Back */
  .back__band {
    position: absolute; left: 0; bottom: 0; width: 100%; height: 76px;
    background: linear-gradient(90deg, var(--yellow) 0%, #f7c40b 45%, var(--orange) 100%);
    border-top: 3px solid var(--silver);
  }
  .back__mark {
    position: absolute; right: 40px; top: 70px; width: 160px;
    font-family: "Tinos", serif; font-size: 20px; line-height: 1.2; text-align: center; color: var(--mark);
  }
  .back__heading {
    position: absolute; left: 38px; top: 16px;
    font-family: "Open Sans", sans-serif; font-size: 20px; color: var(--white);
  }
  .hours {
    position: absolute; left: 38px; top: 46px;
    font-family: "Open Sans", sans-serif; font-size: 15px; color: var(--white);
    border-collapse: collapse;
  }
  .hours td { padding: 0; height: 23px; white-space: pre; }
  .hours--caps { font-weight: 800; }
  .hours--table { left: 31px; top: 43px; font-size: 16px; }
  .hours--table .hours__day { width: 109px; }
  .hours--table .hours__time { font-weight: 700; }
  .hours--inline { font-size: 16px; left: 37px; top: 45px; }
  .hours--inline .hours__time { font-weight: 700; }
  .back__address {
    position: absolute; left: 0; bottom: 10px; width: 100%; text-align: center;
    font-family: "Tinos", serif; font-size: 15px; line-height: 18px; color: var(--ink);
  }
  .back__contact { margin-top: 8px; }
  .back__sep { display: inline-block; width: 1px; height: 15px; background: var(--ink); margin: 0 8px; vertical-align: -2px; }

  .option-label {
    position: absolute; width: 200px; text-align: center;
    font-family: "Open Sans", sans-serif; font-weight: 800; font-size: 21px; color: var(--label);
  }
</style>
</head>
<body>

<section class="card card--front">
  <svg class="front__swoosh" viewBox="0 0 525 300" aria-hidden="true">
    <defs>
      <linearGradient id="goldBand" x1="0" y1="0" x2="1" y2="0">
        <stop offset="0" stop-color="#ffe600"/>
        <stop offset="0.5" stop-color="#f9c20c"/>
        <stop offset="1" stop-color="#e77a1b"/>
      </linearGradient>
    </defs>
    <path d="M0,152 C110,235 260,255 525,182 L525,300 L0,300 Z" fill="#e77a1b"/>
    <path d="M0,160 C110,243 260,262 525,190 L525,300 L0,300 Z" fill="#0b1540"/>
    <path d="M0,172 C110,252 260,268 525,196 L525,300 L0,300 Z" fill="#c9ccd4"/>
    <path d="M0,182 C110,260 270,272 525,203 L525,300 L0,300 Z" fill="#0b1540"/>
    <path d="M0,188 C110,266 270,276 525,208 L525,300 L0,300 Z" fill="url(#goldBand)"/>
  </svg>
  <h1 class="front__name">Dr. Orin Halvey</h1>
  <p class="front__creds">M.B.B.S., F.N.G.F.H.O</p>
  <p class="front__role">Family General Practitioner</p>
  <p class="front__tagline">Caring about your health</p>
  <div class="guild-mark">
    <span class="guild-mark__dot"></span>
    <span>Noble Guild of Family Healers Oceania</span>
  </div>
</section>

<section class="card card--opt1">
  <div class="back__mark">Noble Guild of Family Healers Oceania</div>
  <h2 class="back__heading">Working Hours</h2>
  <table class="hours hours--caps">
    <tr><td>MONDAY  7 AM  - 7 PM</td></tr>
    <tr><td>TUESDAY  7 AM - 12 PM</td></tr>
    <tr><td>WEDNESDAY  7 AM - 10 PM</td></tr>
    <tr><td>THURSDAY  7 AM - 12 PM</td></tr>
    <tr><td>FRIDAY   7 AM  - 8 PM</td></tr>
    <tr><td>SATURDAY  8 AM - 10 PM</td></tr>
    <tr><td>SUNDAY - OFF</td></tr>
  </table>
  <div class="back__band"></div>
  <address class="back__address">
    Upper Level, Harbour Arcade, Ridgeview Plaza Shopping Centre<br>Elmbrook, NSW 2160
    <div class="back__contact">P: 02 5550 1400<span class="back__sep"></span>F: 02 5550 1233</div>
  </address>
</section>
<p class="option-label" style="left:775px; top:338px;">Option# 1</p>

<section class="card card--opt2">
  <div class="back__mark">Noble Guild of Family Healers Oceania</div>
  <h2 class="back__heading" style="left:50px;">Working Hours</h2>
  <table class="hours hours--table">
    <tr><td class="hours__day">Monday</td><td class="hours__time">7 AM  - 7 PM</td></tr>
    <tr><td class="hours__day">Tuesday</td><td class="hours__time">7 AM - 12 PM</td></tr>
    <tr><td class="hours__day">Wednesday</td><td class="hours__time">7 AM - 10 PM</td></tr>
    <tr><td class="hours__day">Thursday</td><td class="hours__time">7 AM - 12 PM</td></tr>
    <tr><td class="hours__day">Friday</td><td class="hours__time">7 AM  - 8 PM</td></tr>
    <tr><td class="hours__day">Saturday</td><td class="hours__time">8 AM - 10 PM</td></tr>
    <tr><td class="hours__day">Sunday</td><td class="hours__time">OFF</td></tr>
  </table>
  <div class="back__band"></div>
  <address class="back__address">
    Upper Level, Harbour Arcade, Ridgeview Plaza Shopping Centre<br>Elmbrook, NSW 2160
    <div class="back__contact">P: 02 5550 1400<span class="back__sep"></span>F: 02 5550 1233</div>
  </address>
</section>
<p class="option-label" style="left:210px; top:679px;">Option# 2</p>

<section class="card card--opt3">
  <div class="back__mark">Noble Guild of Family Healers Oceania</div>
  <h2 class="back__heading">Working Hours</h2>
  <table class="hours hours--inline">
    <tr><td>Monday  <span class="hours__time">7 AM  - 7 PM</span></td></tr>
    <tr><td>Tuesday  <span class="hours__time">7 AM - 12 PM</span></td></tr>
    <tr><td>Wednesday  <span class="hours__time">7 AM - 10 PM</span></td></tr>
    <tr><td>Thursday  <span class="hours__time">7 AM - 12 PM</span></td></tr>
    <tr><td>Friday   <span class="hours__time">7 AM  - 8 PM</span></td></tr>
    <tr><td>Saturday  <span class="hours__time">8 AM - 10 PM</span></td></tr>
    <tr><td>Sunday - <span class="hours__time">OFF</span></td></tr>
  </table>
  <div class="back__band"></div>
  <address class="back__address">
    Upper Level, Harbour Arcade, Ridgeview Plaza Shopping Centre<br>Elmbrook, NSW 2160
    <div class="back__contact">P: 02 5550 1400<span class="back__sep"></span>F: 02 5550 1233</div>
  </address>
</section>
<p class="option-label" style="left:775px; top:686px;">Option# 3</p>

</body>
</html>
```